New Business Card Design Project

Use the flyer uploaded and website www.brightoakbuilders.com for inspiration.
List Our Services on Backside of business cards
Marcus Delling
Harborline Builders Inc.
Licensed General Contractors
858-471-6093

Contact Information for Business Card

Use the flyer uploaded and website www.brightoakbuilders.com for inspiration. List Our Services on Backside of business cards Marcus Delling Harborline Builders Inc. Licensed General Contractors 858-471-6093

```html
<!DOCTYPE html>
<html lang="en">
<head>
<meta charset="utf-8">
<title>Harborline Builders – Business Card</title>
<link rel="stylesheet" href="https://fonts.googleapis.com/css2?family=Roboto:wght@400;500;700;900&display=swap">
<style>
  :root {
    --page-bg: #18181a;
    --card-bg: #222226;
    --brand-red: #ec1c24;
    --brand-blue: #5482c4;
    --ink-white: #f4f4f4;
  }
  * { margin: 0; padding: 0; box-sizing: border-box; }
  html, body {
    width: 1200px; height: 780px; overflow: hidden;
    background: var(--page-bg);
    font-family: "Roboto", Arial, sans-serif;
    color: var(--ink-white);
  }
  .card {
    position: absolute; left: 328px; width: 545px; height: 311px;
    background: var(--card-bg);
    border: 2px solid var(--brand-red);
    border-radius: 26px;
    overflow: hidden;
  }
  .card--back { top: 63px; }
  .card--front { top: 406px; }

  .brand-name {
    position: absolute;
    font-weight: 400;
    letter-spacing: 1.5px;
    text-transform: uppercase;
    color: var(--ink-white);
    white-space: nowrap;
    text-align: center;
  }
  .card--back .brand-name { left: 18px; width: 256px; top: 190px; font-size: 21px; }
  .card--front .brand-name { left: 16px; width: 214px; top: 186px; font-size: 17.5px; }

  .services { position: absolute; left: 335px; top: 48px; }
  .services__heading {
    font-weight: 700; font-size: 14px; line-height: 16.5px;
    color: var(--brand-red); text-transform: uppercase;
  }
  .services__heading--blue { color: var(--brand-blue); margin-bottom: 6px; }
  .services__list { list-style: none; }
  .services__item {
    display: flex; align-items: center; gap: 9px;
    font-size: 11.6px; line-height: 17.3px; letter-spacing: 0.3px;
  }
  .tick { width: 14px; height: 14px; flex: none; }

  .divider {
    position: absolute; left: 270px; top: 55px;
    width: 2px; height: 200px; background: var(--brand-blue);
  }
  .contact { position: absolute; left: 320px; top: 73px; }
  .contact__name {
    font-weight: 700; font-size: 31px; line-height: 32px;
    color: var(--brand-red);
  }
  .contact__role { font-size: 12.2px; letter-spacing: 0.3px; margin-top: 2px; }
  .contact__company { font-size: 12.2px; letter-spacing: 0.2px; margin-top: 27px; }
  .contact__list { list-style: none; margin-top: 15px; }
  .contact__item {
    display: flex; align-items: center; gap: 8px;
    font-size: 12.2px; line-height: 18.5px; letter-spacing: 0.3px;
  }
  .contact__icon { width: 12px; height: 12px; flex: none; }

  .bands { position: absolute; left: 0; top: 270px; width: 545px; height: 22px; }
</style>
</head>
<body>

<section class="card card--back" aria-label="Card back: services">
  <div class="brand-name">Harborline Builders</div>

  <div class="services">
    <p class="services__heading">Our services are<br>100% guaranteed</p>
    <p class="services__heading services__heading--blue">Specializing in:</p>
    <ul class="services__list">
      <li class="services__item"><svg class="tick" viewBox="0 0 14 14"><circle cx="7" cy="7.5" r="5.6" fill="none" stroke="#ec1c24" stroke-width="1.3"/><path d="M4 7.3l2.3 2.4L13 2" fill="none" stroke="#ec1c24" stroke-width="1.5"/></svg>Remodel: Kitchen &amp; Bath</li>
      <li class="services__item"><svg class="tick" viewBox="0 0 14 14"><circle cx="7" cy="7.5" r="5.6" fill="none" stroke="#ec1c24" stroke-width="1.3"/><path d="M4 7.3l2.3 2.4L13 2" fill="none" stroke="#ec1c24" stroke-width="1.5"/></svg>Painting: Interior &amp; Exterior</li>
      <li class="services__item"><svg class="tick" viewBox="0 0 14 14"><circle cx="7" cy="7.5" r="5.6" fill="none" stroke="#ec1c24" stroke-width="1.3"/><path d="M4 7.3l2.3 2.4L13 2" fill="none" stroke="#ec1c24" stroke-width="1.5"/></svg>Flooring: Carpet, Vinyl, Wood</li>
      <li class="services__item"><svg class="tick" viewBox="0 0 14 14"><circle cx="7" cy="7.5" r="5.6" fill="none" stroke="#ec1c24" stroke-width="1.3"/><path d="M4 7.3l2.3 2.4L13 2" fill="none" stroke="#ec1c24" stroke-width="1.5"/></svg>Window &amp; Door Replacement</li>
      <li class="services__item"><svg class="tick" viewBox="0 0 14 14"><circle cx="7" cy="7.5" r="5.6" fill="none" stroke="#ec1c24" stroke-width="1.3"/><path d="M4 7.3l2.3 2.4L13 2" fill="none" stroke="#ec1c24" stroke-width="1.5"/></svg>Plumbing: Repairs &amp; Upgrades</li>
      <li class="services__item"><svg class="tick" viewBox="0 0 14 14"><circle cx="7" cy="7.5" r="5.6" fill="none" stroke="#ec1c24" stroke-width="1.3"/><path d="M4 7.3l2.3 2.4L13 2" fill="none" stroke="#ec1c24" stroke-width="1.5"/></svg>Energy-Efficient Upgrades</li>
      <li class="services__item"><svg class="tick" viewBox="0 0 14 14"><circle cx="7" cy="7.5" r="5.6" fill="none" stroke="#ec1c24" stroke-width="1.3"/><path d="M4 7.3l2.3 2.4L13 2" fill="none" stroke="#ec1c24" stroke-width="1.5"/></svg>Deck &amp; Patio Construction</li>
      <li class="services__item"><svg class="tick" viewBox="0 0 14 14"><circle cx="7" cy="7.5" r="5.6" fill="none" stroke="#ec1c24" stroke-width="1.3"/><path d="M4 7.3l2.3 2.4L13 2" fill="none" stroke="#ec1c24" stroke-width="1.5"/></svg>Water &amp; Mold Damage</li>
      <li class="services__item"><svg class="tick" viewBox="0 0 14 14"><circle cx="7" cy="7.5" r="5.6" fill="none" stroke="#ec1c24" stroke-width="1.3"/><path d="M4 7.3l2.3 2.4L13 2" fill="none" stroke="#ec1c24" stroke-width="1.5"/></svg>Garage Renovation</li>
    </ul>
  </div>
</section>

<section class="card card--front" aria-label="Card front: contact">
  <div class="brand-name">Harborline Builders</div>
  <div class="divider"></div>

  <div class="contact">
    <h1 class="contact__name">Marcus Delling</h1>
    <p class="contact__role">Licensed General Contractors</p>
    <p class="contact__company">Harborline Builders Inc.</p>
    <ul class="contact__list">
      <li class="contact__item"><svg class="contact__icon" viewBox="0 0 12 12"><path d="M2.5 1l2 2.3-1 1.3c.7 1.5 1.9 2.7 3.4 3.4l1.3-1 2.3 2-1.1 1.5C5.3 10.3 1.7 6.7 1.1 2.1z" fill="#ec1c24"/></svg>858-471-6093</li>
      <li class="contact__item"><svg class="contact__icon" viewBox="0 0 12 12"><rect x="1" y="3" width="10" height="7.5" rx="1" fill="#ec1c24"/><path d="M1.5 3.5L6 7l4.5-3.5" fill="none" stroke="#222226" stroke-width="1"/></svg>info@brightoakbuilders.com</li>
      <li class="contact__item"><svg class="contact__icon" viewBox="0 0 12 12"><circle cx="6" cy="6" r="5.2" fill="#ec1c24"/><path d="M1 6h10M6 .8c-2 2.9-2 7.5 0 10.4M6 .8c2 2.9 2 7.5 0 10.4" fill="none" stroke="#222226" stroke-width=".8"/></svg>www.brightoakbuilders.com</li>
    </ul>
  </div>

  <svg class="bands" viewBox="0 0 545 22" preserveAspectRatio="none" aria-hidden="true">
    <path d="M0 0H240c6 0 10 1 14 4l22 16H0z" fill="#ec1c24"/>
    <path d="M264 0H545V20H300c-6 0-9-1-13-4z" fill="#5482c4"/>
  </svg>
</section>

</body>
</html>
```